Specialised investor in e-mobility and energy wants business card design

We need a business card design that fits our existing corporate design. <The look and feel must be 'sharp'/'clean', dynamic, communicate momentum, professionalism etc (as one would imagine from a firm in the financial sector). We like the idea of a reverse-side of the card that includes the logo, and the name and contact details on the other. We expect the deliverable to be whatever format might be required to be able to get cards printed directly by a service such as kelmo press. Our website is www.zub.capital

```html
<!DOCTYPE html>
<html lang="en">
<head>
<meta charset="utf-8">
<title>ZUB Capital – Business Card</title>
<link rel="stylesheet" href="https://fonts.googleapis.com/css2?family=Montserrat:wght@500;700&family=Arimo:wght@400&display=swap">
<style>
  :root {
    --page: #2b2b2b;
    --forest: #2f4d22;
    --forest-deep: #253f1a;
    --leaf: #86b54a;
    --paper: #ffffff;
    --ink: #333333;
  }
  * { box-sizing: border-box; margin: 0; padding: 0; }
  html, body { width: 1200px; height: 900px; overflow: hidden; }
  body {
    background: var(--page);
    display: flex;
    flex-direction: column;
    align-items: center;
    justify-content: center;
    gap: 30px;
    font-family: "Arimo", Arial, sans-serif;
  }
  .card {
    position: relative;
    width: 700px;
    height: 400px;
    border-radius: 22px;
    overflow: hidden;
  }
  .card-front { background: var(--paper); }
  .front-swoosh { position: absolute; inset: 0; width: 100%; height: 100%; }
  .brand-name {
    position: absolute;
    font-family: "Montserrat", Arial, sans-serif;
    font-weight: 500;
    letter-spacing: 1px;
  }
  .card-front .brand-name {
    left: 70px;
    top: 120px;
    font-size: 40px;
    color: var(--forest);
  }
  .divider {
    position: absolute;
    left: 380px;
    top: 95px;
    width: 1.5px;
    height: 200px;
    background: var(--forest);
  }
  .contact-block {
    position: absolute;
    left: 405px;
    top: 100px;
    color: var(--ink);
  }
  .person-name {
    font-family: "Montserrat", Arial, sans-serif;
    font-weight: 700;
    font-size: 24px;
    color: var(--forest);
    letter-spacing: 0.5px;
  }
  .person-name .surname { color: var(--leaf); }
  .person-role { font-size: 14px; margin: 2px 0 10px; }
  .address { font-size: 14px; line-height: 1.35; margin-bottom: 10px; }
  .contact-list { list-style: none; font-size: 14px; line-height: 1.6; }
  .contact-list li { display: flex; align-items: center; gap: 8px; }
  .contact-icon { width: 12px; height: 12px; flex: none; }
  .card-back { background: var(--forest); }
  .pattern-field {
    position: absolute;
    inset: 0;
    background: linear-gradient(135deg, var(--forest) 0%, var(--forest-deep) 50%, var(--forest) 100%);
  }
  .card-back .brand-name {
    left: 50%;
    top: 50%;
    transform: translate(-50%, -50%);
    font-size: 52px;
    color: var(--paper);
    white-space: nowrap;
  }
</style>
</head>
<body>
  <section class="card card-front">
    <svg class="front-swoosh" viewBox="0 0 700 400" aria-hidden="true">
      <path d="M0,262 C190,300 440,320 600,400 L0,400 Z" fill="var(--forest)"/>
      <path d="M0,252 C190,290 440,312 600,400" fill="none" stroke="var(--leaf)" stroke-width="7"/>
    </svg>
    <div class="brand-name">ZUB Capital</div>
    <div class="divider"></div>
    <div class="contact-block">
      <h1 class="person-name">TOBIAS <span class="surname">RENNER</span></h1>
      <p class="person-role">Director/Founder</p>
      <p class="address">1234 Street Name<br>Country Name AB 5748</p>
      <ul class="contact-list">
        <li>
          <svg class="contact-icon" viewBox="0 0 12 12" aria-hidden="true"><path d="M2 1h2.5l1 3-1.5 1a6 6 0 0 0 3 3l1-1.5 3 1V11a1 1 0 0 1-1 1A10 10 0 0 1 1 2a1 1 0 0 1 1-1z" fill="var(--leaf)"/></svg>
          123-480-2291
        </li>
        <li>
          <svg class="contact-icon" viewBox="0 0 12 12" aria-hidden="true"><rect x="0" y="2" width="12" height="8" fill="var(--leaf)"/><path d="M0 2l6 4.5L12 2" fill="none" stroke="var(--paper)" stroke-width="1"/></svg>
          info@zub.capital
        </li>
        <li>
          <svg class="contact-icon" viewBox="0 0 12 12" aria-hidden="true"><circle cx="6" cy="6" r="5.5" fill="var(--leaf)"/><path d="M0.5 6h11M6 0.5c-3 3-3 8 0 11M6 0.5c3 3 3 8 0 11" fill="none" stroke="var(--paper)" stroke-width="0.8"/></svg>
          www.zub.capital
        </li>
      </ul>
    </div>
  </section>

  <section class="card card-back">
    <div class="pattern-field" role="img" aria-label="Tone-on-tone repeating brand pattern in dark and mid green"></div>
    <div class="brand-name">ZUB Capital</div>
  </section>
</body>
</html>
```